Oil Field Service company needs professional business cards

Looking to clean up our current company business cards and look a little more professional. Brenwick Casing Services is a US based company that services the oil field. We deal with engineers, managers and oil rigs....................................................................................................................................................................................................................................................................................................................................................................................................

Target Market(s)

Oil and Gas professionals

Industry/Entity Type

Oil And Gas

Contact Information for Business Card

See attached photo as example

Font styles to use
Sans Serif

Colors
ec1f27

Requirements
Must have
• Company Logo, Name, Title, Cell, Office, Fax, Email.
• See attached photo
Nice to have
• External CRT, Internal CRT, Casing Crews, Torque Turn, Laydown Machine
Should not have
• Do not introduce any new pictures and keep it professional looking

```html
<!DOCTYPE html>
<html lang="en">
<head>
<meta charset="utf-8">
<title>Brenwick Casing Services – Business Card</title>
<link rel="stylesheet" href="https://fonts.googleapis.com/css2?family=Source+Sans+3:wght@400;600;700&display=swap">
<style>
  :root {
    --brand-red: #ec1f27;
    --slate: #4b5863;
    --slate-dark: #3e4a54;
    --ink: #5a6670;
    --paper: #ffffff;
    --backdrop: #e9e7e3;
    --rule: #c9cdd1;
  }
  * { box-sizing: border-box; margin: 0; padding: 0; }
  html, body { width: 1200px; height: 950px; overflow: hidden; }
  body {
    background: var(--backdrop);
    font-family: "Source Sans 3", "Helvetica Neue", Arial, sans-serif;
    position: relative;
  }
  .card {
    position: absolute;
    left: 250px;
    width: 700px;
    height: 400px;
    border-radius: 4px;
    overflow: hidden;
    box-shadow: 0 6px 18px rgba(0,0,0,.15);
  }
  .card--back { top: 50px; background: linear-gradient(135deg, var(--slate) 0%, var(--slate-dark) 100%); }
  .card--front { top: 500px; background: var(--paper); }

  .wordmark {
    position: absolute;
    display: flex;
    align-items: center;
    gap: 12px;
    font-weight: 700;
    font-size: 27px;
    letter-spacing: .5px;
    white-space: nowrap;
  }
  .wordmark__dot { width: 14px; height: 14px; border-radius: 50%; background: var(--brand-red); flex: none; }
  .card--back .wordmark { left: 40px; top: 184px; color: var(--paper); }
  .card--front .wordmark { left: 40px; top: 250px; color: var(--slate); }

  .divider {
    position: absolute;
    width: 1px;
    background: var(--rule);
  }
  .card--back .divider { left: 405px; top: 70px; height: 230px; background: rgba(255,255,255,.35); }
  .card--front .divider { left: 405px; top: 60px; height: 220px; }

  .services {
    position: absolute;
    left: 440px; top: 80px;
    list-style: none;
    color: var(--paper);
    font-size: 19px;
    line-height: 34px;
  }
  .services li::before {
    content: "";
    display: inline-block;
    width: 7px; height: 7px;
    background: var(--brand-red);
    border-radius: 50%;
    margin-right: 12px;
    vertical-align: middle;
  }

  .contact {
    position: absolute;
    left: 435px; top: 52px;
    color: var(--ink);
    font-size: 17px;
    line-height: 26px;
  }
  .contact__name { color: var(--brand-red); font-size: 27px; font-weight: 600; line-height: 34px; }
  .contact__meta { margin-bottom: 8px; }
  .contact__list { list-style: none; }
  .contact__list li { display: flex; align-items: center; gap: 10px; }
  .contact__list svg { width: 15px; height: 15px; flex: none; fill: var(--brand-red); }

  .wave { position: absolute; left: 0; top: 0; width: 700px; height: 400px; }
</style>
</head>
<body>

<section class="card card--back" aria-label="Card back">
  <div class="wordmark"><span class="wordmark__dot"></span>Brenwick Casing Services</div>
  <div class="divider"></div>
  <ul class="services">
    <li>External CRT</li>
    <li>Internal CRT</li>
    <li>Casing Crews</li>
    <li>Torque Turn</li>
    <li>Laydown Machine</li>
  </ul>
</section>

<section class="card card--front" aria-label="Card front">
  <svg class="wave" viewBox="0 0 700 400" aria-hidden="true">
    <path d="M700,175 C690,300 520,350 250,400 L700,400 Z" fill="var(--slate)"/>
    <path d="M110,400 C420,372 645,322 688,178 C668,318 470,378 230,400 Z" fill="var(--brand-red)"/>
  </svg>
  <div class="wordmark"><span class="wordmark__dot"></span>Brenwick Casing Services</div>
  <div class="divider"></div>
  <div class="contact">
    <p class="contact__name">Cody Harlan</p>
    <p>Area Manager</p>
    <p class="contact__meta">Redfield, OK 73899</p>
    <ul class="contact__list">
      <li><svg viewBox="0 0 16 16"><path d="M3 1l3 3-1.5 2a9 9 0 0 0 5.5 5.5L12 10l3 3-2 2C7 15 1 9 1 3z"/></svg>(555)210-4400</li>
      <li><svg viewBox="0 0 16 16"><path d="M4 0h8a1 1 0 0 1 1 1v14a1 1 0 0 1-1 1H4a1 1 0 0 1-1-1V1a1 1 0 0 1 1-1zm1 2v10h6V2z"/></svg>(555)318-6621</li>
      <li><svg viewBox="0 0 16 16"><path d="M4 1h7v4H4zM1 6h14v7h-3v2H4v-2H1zm4 5v3h6v-3z"/></svg>(555)210-4487</li>
      <li><svg viewBox="0 0 16 16"><path d="M1 3h14v10H1zm1 1.5V5l6 4 6-4v-.5z"/></svg>cody@brenwick.com</li>
      <li><svg viewBox="0 0 16 16"><circle cx="8" cy="8" r="7"/></svg>www.brenwick.com</li>
    </ul>
  </div>
</section>

</body>
</html>
```